Medical VIP club - small design

Please read the specs in a design brief attached. Also we don't have logo in a Vector format and attaching the only version we have.

Club

```html
<!DOCTYPE html>
<html lang="en">
<head>
<meta charset="utf-8">
<title>Veltara VIP Club</title>
<link href="https://fonts.googleapis.com/css2?family=Gelasio:ital,wght@0,400;0,600;0,700;1,400;1,600&display=swap" rel="stylesheet">
<style>
:root{
  --bg-deep:#2c261b;
  --bg-mid:#4d4535;
  --bg-glow:#5d5442;
  --topbar:#2a2419;
  --footer:#2b251b;
  --panel:#cbc1a7;
  --panel-light:#d3cab1;
  --panel-edge:#9c8f70;
  --ink:#33291b;
  --ink-soft:#4a3e2b;
  --gold:#e3cc93;
  --cream:#f2ead6;
  --foot-link:#a89a78;
  --dot-border:#6e6450;
  --hero-top:#c9a772;
  --hero-bottom:#a98558;
}
*{margin:0;padding:0;box-sizing:border-box}
html,body{width:1200px;height:1096px;overflow:hidden}
body{
  position:relative;
  font-family:"Gelasio",Georgia,serif;
  background:radial-gradient(ellipse 70% 55% at 50% 35%,var(--bg-glow),var(--bg-mid) 55%,var(--bg-deep));
  color:var(--ink);
}
.top-bar{position:absolute;left:0;top:0;width:1200px;height:40px;background:var(--topbar);border-bottom:1px solid #5a503c}
.top-bar a{position:absolute;top:11px;font-style:italic;font-weight:700;font-size:17px;color:var(--gold);text-decoration:none}
.top-bar .reg{left:890px}
.top-bar .sign{left:1016px;font-weight:600;text-decoration:underline}
.brand{position:absolute;left:130px;top:84px;display:flex;align-items:center;gap:10px}
.brand-mark{width:22px;height:22px;border-radius:50%;background:var(--gold)}
.brand-name{font-size:40px;font-weight:600;color:var(--gold);line-height:1}
.contact{position:absolute;left:955px;top:82px;height:53px;border-left:2px solid var(--gold);padding-left:14px;color:var(--cream)}
.contact h3{font-size:20px;font-weight:700;line-height:1.2}
.contact p{font-size:19px;line-height:1.2}
.panel{position:absolute;left:130px;top:158px;width:967px;height:818px;background:linear-gradient(180deg,var(--panel-light),var(--panel));border:1px solid var(--panel-edge);box-shadow:0 0 14px rgba(0,0,0,.45)}
.nav{position:absolute;left:0;top:0;width:100%;height:36px;display:flex;align-items:center;border-bottom:3px solid #8f815f}
.nav a{font-size:17px;color:var(--ink);text-decoration:none;text-align:center;border-right:1px solid var(--ink);line-height:17px}
.nav a:last-child{border-right:none}
.nav .strong{font-weight:700}
.slide{position:absolute;left:10px;top:58px;width:944px;height:351px;border:2px solid #3a3122;background:linear-gradient(180deg,var(--hero-top),var(--hero-bottom))}
.dots{position:absolute;left:368px;top:421px;display:flex;gap:8px;align-items:center}
.dots span{width:20px;height:20px;border:1.5px solid var(--dot-border);border-radius:3px}
.dots .on{width:27px;height:27px;background:#7a705c;border-color:#5e5543}
.rule{position:absolute;left:10px;top:450px;width:944px;border-top:2px dotted #6a5f48}
.side-title{position:absolute;left:29px;top:548px;font-size:21px;font-style:italic;font-weight:600;color:var(--ink)}
.side-line{position:absolute;left:153px;top:519px;height:106px;border-left:2px solid var(--ink)}
.club-title{position:absolute;left:196px;top:472px;font-size:18px;font-style:italic;font-variant:small-caps;font-weight:600;color:var(--ink)}
.copy{position:absolute;left:196px;top:516px;width:740px;font-size:13.4px;font-style:italic;line-height:17px;color:var(--ink-soft)}
.copy p+p{margin-top:17px}
.follow{position:absolute;left:770px;top:788px;font-size:15px;color:var(--ink)}
.social{position:absolute;left:861px;top:778px;display:flex;gap:4px}
.social span{width:27px;height:27px;border-radius:3px;background:#8a7c5c;border:1px solid #6c614a}
.footer{position:absolute;left:0;top:976px;width:1200px;height:120px;background:var(--footer)}
.foot-links{position:absolute;left:138px;top:46px;font-size:15px;color:var(--foot-link)}
.foot-links a{color:var(--foot-link);text-decoration:none}
.foot-links .sep{margin:0 5px}
.foot-links .strong{font-weight:700}
.copyright{position:absolute;left:696px;top:46px;font-size:15px;color:var(--foot-link)}
.foot-brand{position:absolute;left:975px;top:34px;display:flex;align-items:center;gap:7px}
.foot-brand .brand-mark{width:16px;height:16px}
.foot-brand .brand-name{font-size:28px}
</style>
</head>
<body>
<header class="top-bar">
  <a class="reg" href="#">Registration</a>
  <a class="sign" href="#">Sign In</a>
</header>
<div class="brand"><span class="brand-mark"></span><span class="brand-name">veltara</span></div>
<div class="contact"><h3>Contact Us</h3><p>01480-552-310</p></div>

<main class="panel">
  <nav class="nav">
    <a href="#" style="width:104px">Home</a>
    <a href="#" class="strong" style="width:140px">About Us</a>
    <a href="#" style="width:140px">V.I.P Club</a>
    <a href="#" style="width:154px">Services</a>
    <a href="#" style="width:239px">Packages and Prices</a>
    <a href="#" class="strong" style="width:190px">Registration</a>
  </nav>
  <div class="slide" role="img" aria-label="Photo of an elegant hotel lobby"></div>
  <div class="dots"><span></span><span></span><span class="on"></span><span></span><span></span><span></span><span></span><span></span></div>
  <div class="rule"></div>
  <h2 class="side-title">About Us</h2>
  <div class="side-line"></div>
  <h1 class="club-title">Veltara V.I.P Club</h1>
  <div class="copy">
    <p>Background design is needed for a medical company that offers a membership in an Israeli medical center. The membership allows people to receive priority treatment (booking of best hotels, free consultations throughout the year and priority appointment for top Israeli doctors). Therefore target market are affluent Russian people.<br>Client seems to like this particular scheme, so all we need is to pretty it up and to create more concepts with different colors.</p>
    <p>Background design is needed for a medical company that offers a membership in an Israeli medical center. The membership allows people to receive priority treatment (booking of best hotels, free consultations throughout the year and priority appointment for top Israeli doctors). Therefore target market are affluent Russian people. Client seems to like this particular scheme, so all we need is to pretty it up and to create more concepts with different colors.</p>
  </div>
  <div class="follow">Follow us</div>
  <div class="social"><span></span><span></span><span></span></div>
</main>

<footer class="footer">
  <div class="foot-links"><a href="#">Home</a><span class="sep">|</span><a href="#">Vip Club</a><span class="sep">|</span><a href="#">Services</a><span class="sep">|</span><a href="#">Packages and Prices</a><span class="sep">|</span><a href="#" class="strong">Registration</a></div>
  <div class="copyright">© All Rights Reserved 2011 Veltara</div>
  <div class="foot-brand"><span class="brand-mark"></span><span class="brand-name">veltara</span></div>
</footer>
</body>
</html>
```